I need a letterhead for a newsletter that will go out quarterly to the dentists of the 18th district. It is called "The Crestline Digest" We are in Amarillo TX and have this landmark in the photo as our most prominent feature. If it could be used, that would be cool.
This is a professional organization newsletter so the letterhead should be somewhat professional.

Target Market(s)

Dentists

Industry/Entity Type

Dental

Font styles to use
Serif

Colors

Designer to choose only greyscale colors for use in the design.

Requirements
Must have
• I want the title of "The Crestline Digest" to be the on top with the phrase "Cobalt Ridge Dental Society" written underneath.
Nice to have
• the photo incorporated could be incorporated in black and white or color along the bottom of the letterhead or with the title inside the photo.
Should not have
• I don't want it to be cartoony. I want it to be stylish and elegant and professional.

```html
<!DOCTYPE html>
<html lang="en">
<head>
<meta charset="utf-8">
<title>The Crestline Digest – Letterhead</title>
<link href="https://fonts.googleapis.com/css2?family=Cinzel:wght@400;500&family=Questrial&family=Lato:wght@400&display=swap" rel="stylesheet">
<style>
  :root{
    --backdrop:#d9dfe8;
    --paper:#f7f7f7;
    --photo-light:#d6d6d6;
    --photo-mid:#b4b4b4;
    --photo-dark:#8e8e8e;
    --title-blue:#2a14e6;
    --ink:#2b2b2b;
    --ink-soft:#4a4a4a;
    --band-navy:#262064;
    --band-text:#e9e8f4;
  }
  *{box-sizing:border-box;margin:0;padding:0}
  html,body{width:1200px;height:898px;overflow:hidden}
  body{background:var(--backdrop);display:flex;align-items:center;justify-content:center}
  .letterhead{
    position:relative;width:608px;height:860px;background:var(--paper);
    box-shadow:0 4px 18px rgba(40,50,70,.18);overflow:hidden;
  }
  .masthead{position:absolute;left:0;top:0;width:100%;height:330px}
  .masthead-photo{
    position:absolute;inset:0;
    background:
      linear-gradient(100deg,transparent 0 76%,var(--photo-dark) 76% 100%),
      linear-gradient(180deg,var(--photo-light) 0%,#c7c7c7 45%,var(--photo-mid) 70%,var(--photo-dark) 100%);
  }
  .masthead-title{
    position:absolute;left:0;right:0;top:150px;text-align:center;
    font-family:'Cinzel',serif;font-weight:400;color:var(--title-blue);line-height:1.1;
  }
  .masthead-title .name{display:block;font-size:30px;font-weight:400;padding-left:50px}
  .masthead-title .society{display:block;font-size:19px;font-weight:400;margin-top:4px}
  .letter{
    position:absolute;left:68px;right:62px;top:352px;
    font-family:'Questrial',sans-serif;color:var(--ink);font-size:12.5px;line-height:1.5;
  }
  .letter .body{text-align:justify}
  .letter .body + .body{margin-top:18px}
  .signature{margin-top:6px;margin-left:auto;width:max-content;font-family:'Questrial',sans-serif}
  .signature .signer{font-size:16px;color:var(--ink);line-height:1.3}
  .signature .role{font-size:10.5px;color:var(--ink-soft);padding-left:10px;line-height:1.4}
  .contact-band{position:absolute;left:0;bottom:0;width:100%;height:66px}
  .contact-band svg.band-shape{position:absolute;inset:0}
  .contact-list{
    position:absolute;left:40px;right:30px;bottom:12px;display:flex;justify-content:space-between;
    list-style:none;font-family:'Lato',sans-serif;font-size:12px;letter-spacing:.6px;color:var(--band-text);
  }
  .contact-item{position:relative;padding-top:4px;text-align:center}
  .contact-icon{
    position:absolute;left:50%;top:-30px;transform:translateX(-50%);
    width:20px;height:20px;border-radius:50%;background:var(--band-navy);
    border:2px solid var(--paper);display:flex;align-items:center;justify-content:center;
  }
</style>
</head>
<body>
<main class="letterhead">
  <header class="masthead">
    <div class="masthead-photo" role="img" aria-label="Black and white photo of a tall layered sandstone rock spire rising above a canyon, with a cliff wall on the right"></div>
    <h1 class="masthead-title">
      <span class="name">The Crestline Digest</span>
      <span class="society">Cobalt Ridge Dental Society</span>
    </h1>
  </header>

  <section class="letter">
    <p class="greeting">Hello Sir/Mam</p>
    <p class="body">Lorem ipsum dolor sit amet, consectetur adipiscing elit. Donec orci purus, luctus vitae dignissim eu, iaculis sed purus. Vivamus faucibus, ipsum nec aliquet viverra, leo mauris condimentum ligula, sit amet sagittis enim ligula quis arcu. Nam egestas tortor id nisi porttitor mattis. In tortor ante, ultricies in suscipit a, tempus non massa. Vivamus et auctor mi. Fusce vel massa nulla. Phasellus nec eros mauris, et scelerisque orci. Donec malesuada orci vitae nulla accumsan porta a id massa.</p>
    <p class="body">Quisque accumsan iaculis magna sit amet fringilla. Maecenas consequat, magna eget tincidunt semper, odio nibh rutrum mi, id feugiat ante nisi eu risus. Vestibulum nunc orci, rhoncus a placerat in, ultricies in mi. Cras mattis varius eros, vel fringilla nisi suscipit eget. Quisque scelerisque sagittis nulla at porttitor. Mauris a justo et tellus interdum tristique. Sed id augue vitae urna euismod commodo aliquet a quam. Pellentesque arcu velit, cursus et malesuada ut, consequat et diam. Nullam erat sem, rhoncus id ullamcorper vitae, rhoncus et arcu. In ultricies ultricies nulla,</p>

    <div class="signature">
      <p class="signer">Dana Whitlow</p>
      <p class="role">Co-Founder &amp; CEO</p>
    </div>
  </section>

  <footer class="contact-band">
    <svg class="band-shape" width="608" height="66" viewBox="0 0 608 66" aria-hidden="true">
      <polygon points="22,0 580,0 608,22 608,66 0,66" fill="var(--band-navy)"/>
    </svg>
    <ul class="contact-list">
      <li class="contact-item">
        <span class="contact-icon"><svg width="10" height="10" viewBox="0 0 10 10"><path d="M2 1l2 0 .6 2-1.2.8a5 5 0 0 0 2.8 2.8L7 5.4 9 6v2c0 .6-.4 1-1 1A8 8 0 0 1 1 2c0-.6.4-1 1-1z" fill="#fff"/></svg></span>
        (555) 014-2290
      </li>
      <li class="contact-item">
        <span class="contact-icon"><svg width="10" height="10" viewBox="0 0 10 10"><rect x="1" y="2.5" width="8" height="5.5" fill="#fff"/><path d="M1 2.5l4 3 4-3" stroke="var(--band-navy)" stroke-width="1" fill="none"/></svg></span>
        info@crestlinedigest.org
      </li>
      <li class="contact-item">
        <span class="contact-icon"><svg width="10" height="10" viewBox="0 0 10 10"><circle cx="5" cy="5" r="3.8" stroke="#fff" fill="none"/><path d="M1.2 5h7.6M5 1.2c-2 2.2-2 5.4 0 7.6M5 1.2c2 2.2 2 5.4 0 7.6" stroke="#fff" stroke-width=".8" fill="none"/></svg></span>
        www.crestlinedigest.org
      </li>
    </ul>
  </footer>
</main>
</body>
</html>
```